need corporate, modern business card created for Consulting Company

I need a slick business card using elements from my website, as well as, integrating my pixelforge-created logo (see files).

The business card needs to be:
1. Corporate and modern
2. Clean and professional

I've included a PSD with the logo/icon that you can use to create it. Feel free to try a metallic finish on the logo, make it bigger/small, underlay it. Whatever you need to do to make my card stand out.

Try a black background, or white background or gray.

The idea is for my card to be memorable as well as professional and corporate.

Target Market(s)

Corporate business in the US and Canada.

Industry/Entity Type

Business

Contact Information for Business Card

Commerce Advancing Methods
Martin Coles, Senior Partner
office: 1 877 555 0143
mobile: 1 519 555 0172
website: http://www.brightvale.example

Requirements
Must have
• Card-related information
• corporate, yet modern
• clean and professional
• incorporate the icon only
• must have an editable form when complete!
Nice to have
• metallic icon might be cool
• try it with white or black

```html
<!DOCTYPE html>
<html lang="en">
<head>
<meta charset="utf-8">
<title>Brightvale Business Card</title>
<link href="https://fonts.googleapis.com/css2?family=Questrial&family=Mulish:ital,wght@0,400;0,600;1,700&display=swap" rel="stylesheet">
<style>
  :root {
    --backdrop: #3a322e;
    --card: #141414;
    --card-edge: #222222;
    --silver: #c9c9c9;
    --blue: #2f6fd0;
    --white: #f2f2f2;
    --muted: #bdbdbd;
    --rule: #8a8a8a;
  }
  * { margin: 0; padding: 0; box-sizing: border-box; }
  html, body { width: 1200px; height: 780px; overflow: hidden; }
  body {
    background: var(--backdrop);
    font-family: "Mulish", Arial, sans-serif;
    display: flex;
    align-items: center;
    justify-content: center;
    gap: 48px;
  }
  .card {
    width: 520px;
    height: 297px;
    background: var(--card);
    border: 1px solid var(--card-edge);
    border-radius: 4px;
    position: relative;
    box-shadow: 0 18px 40px rgba(0,0,0,.45);
  }
  /* back side */
  .card-back { display: flex; align-items: center; justify-content: center; }
  .wordmark {
    font-family: "Questrial", Arial, sans-serif;
    display: flex;
    align-items: center;
    gap: 14px;
  }
  .wordmark-mark { width: 26px; height: 26px; }
  .card-back .wordmark-name { font-size: 64px; color: var(--silver); letter-spacing: 1px; }
  .card-back .wordmark-mark { background: var(--silver); }

  /* front side */
  .card-front .brand {
    position: absolute;
    top: 46px;
    right: 42px;
    text-align: left;
  }
  .card-front .wordmark-name { font-size: 58px; color: var(--blue); line-height: 1; }
  .card-front .wordmark-mark { background: var(--blue); }
  .tagline {
    font-size: 15px;
    color: var(--white);
    margin-top: 6px;
    margin-left: 40px;
    letter-spacing: .3px;
  }
  .details {
    position: absolute;
    left: 40px;
    right: 30px;
    bottom: 40px;
    display: flex;
    align-items: stretch;
  }
  .person { text-align: right; padding-right: 22px; border-right: 1px solid var(--rule); }
  .person-name { font-style: italic; font-weight: 700; font-size: 21px; color: var(--blue); }
  .person-title { font-size: 15px; color: var(--white); margin-top: 2px; }
  .person-web { font-size: 14px; color: var(--white); margin-top: 8px; }
  .contacts { list-style: none; padding-left: 22px; font-size: 15px; color: var(--white); }
  .contacts li { display: flex; align-items: center; gap: 10px; margin: 3px 0; }
  .contact-icon { width: 18px; height: 18px; flex: none; }
</style>
</head>
<body>
  <section class="card card-back" aria-label="Card back">
    <div class="wordmark">
      <span class="wordmark-mark"></span>
      <span class="wordmark-name">brightvale</span>
    </div>
  </section>

  <section class="card card-front" aria-label="Card front">
    <div class="brand">
      <div class="wordmark">
        <span class="wordmark-mark"></span>
        <span class="wordmark-name">brightvale</span>
      </div>
      <p class="tagline">Commerce Advancing Methods</p>
    </div>

    <div class="details">
      <div class="person">
        <p class="person-name">Martin Coles</p>
        <p class="person-title">Senior Partner</p>
        <p class="person-web">www.brightvale.example</p>
      </div>
      <ul class="contacts">
        <li>
          <svg class="contact-icon" viewBox="0 0 18 18" aria-hidden="true">
            <rect width="18" height="18" rx="3" fill="#2f6fd0"/>
            <path d="M5 4l2.2 0 1 2.6-1.3 1a6 6 0 0 0 3.5 3.5l1-1.3 2.6 1V13a1 1 0 0 1-1 1A9 9 0 0 1 4 5a1 1 0 0 1 1-1z" fill="#fff"/>
          </svg>
          1 877 555 0143
        </li>
        <li>
          <svg class="contact-icon" viewBox="0 0 18 18" aria-hidden="true">
            <rect width="18" height="18" rx="3" fill="#2f6fd0"/>
            <rect x="6" y="3" width="6" height="12" rx="1" fill="#fff"/>
            <rect x="7" y="4.5" width="4" height="7" fill="#2f6fd0"/>
          </svg>
          1 519 555 0172
        </li>
        <li>
          <svg class="contact-icon" viewBox="0 0 18 18" aria-hidden="true">
            <rect width="18" height="18" rx="3" fill="#2f6fd0"/>
            <rect x="3" y="5" width="12" height="8" fill="#fff"/>
            <path d="M3 5l6 5 6-5" fill="none" stroke="#2f6fd0" stroke-width="1.2"/>
          </svg>
          info@brightvale.example
        </li>
      </ul>
    </div>
  </section>
</body>
</html>
```